Nutritional & Gastrointestinal Health Consulting Service-Website design

We need a website design for a new health consulting service called "Bright Vale" based in Perth, Australia.

We will be providing consulting services in the areas of:
1) Nutrition and Diet
2) Gastrointestinal Health (which means stomach & digestive system related health)

These consulting services will be provided by an Accredited Dietitian and a Paediatric Gastroenterologist.

We are open to creative ideas in terms of design, layout, fonts and colours. We also would love to see images of nature in the backdrop with families (adults with kids) having a good time, fresh fruits and vegetables displayed in a farmer's market or supermarket. 2 or 3 images should be sufficient. We would also definitely want our logo somewhere in the main page of website. The logo file is also attached. Please have a look at a website's design that we really liked. We would love to see designs inspired by that style. The website details are in the in the "nice to have priorities" section of this project brief.

We also would be looking at website designers with software coding skills so that if we like the design we can go ahead with the next step of coding.

The website design should communicate the purpose of the website and at the same time be simple, elegant and unique/eye-catching.

We look forward to receiving creative ideas for our website from you all. Good luck!

More details have been added to our project- for example: Logo, fonts style, must haves etc etc. Please view the updated project brief. Looking forward to receiving your fantastic ideas for our website. Thanking you

Hi, I have updated the colour preference. Will add the content preferences tomorrow. thanks

Hello all, I have now added a LOT more content to what we want in our website. It is very much in detail, so please carefully have a read through the entire project brief. If you have any questions write back to me and I will try to respond as quickly as I can. Last few days were busy so couldn't respond quickly to all of you who had send me designs/queries/questions. Thank you for your patience. I look forward to receiving fantastic designs from you all. Good Luck :-)

Target Market(s)

Adults based in western speaking countries aged 18 to 60 years

Industry/Entity Type

Software

Font styles to use
Sans Serif
Script

Colors
faa54b
acd036

Requirements
Must have
• The website must have the MAIN logo file attached. I have attached 3 files: 1) MAIN logo; 2) supplementary logo A ; 3) supplementary logo B

I have selected 2 colours from the colour scheme (see below)-(as the colour of our logo is that).
However we would also like to see LIGHT CHOCOLATE BROWN or CHOCOLATE BROWN colour used as the background colour of the website
Preferred WEBSITE CONTENT:
1) HOME PAGE:
Content required=
--Company Logo
--Dr Dorian Pelham
Paediatric Gastroenterologist & Hepatologist
-Marla Pelham.
Dietitian & Nutritionist
--Website Menu (either listed horizontally or vertically):
Once clicked on each name:

Under each of the Website Menu items we want the following Headings to be added

2) ABOUT US page:
Sub-heading under this: Qualification, Skills, Special Interest

3) SERVICES
DORIAN'S PAGE: Individual Consultation, Endoscopy procedures
Individual Consultation, Group Based Services, Food Diary, Food & Symptom Diary

4) FEES & REBATE: Content as below:
Please Note: Payment of full fees is required at the time of consultation and procedures. 48 hours notice is required for cancellation of appointments/non-attendance. Failure to provide this may result in a fee being incurred. Please call reception to find out the amount of fee charged for cancellation of appointments/non-attendance.
headings are:
Paediatric Gastroenterology:
Dorian's pge
Individual Consultation - Initial (upto 30 mins):
Review Consultation (upto 15 mins):
Endoscopy procedures - No Gap fees charged. Fees will be billed directly to Vitacover. If any queries, please contact reception.

marla's pge
sub heading:
Individual Consultation - Initial (upto 45 mins):
Individual Consultation - Review (upto 30 mins):

Concession-Individual Consultation -Initial (upto 45 mins):
Concession-Individual Consultation - Review (upto 30 mins):
Please Note: Concession applies for health care card holders & pensioners

Group Based Services: Pricing subject to the type of service provided. Please contact us for an obligation free quote.
Education Topics Include:
- Paediatric Nutrition (Introducing Solids, Fussy Eating, Healthy Eating)
- Pregnancy Nutrition, Gestational Diabetes, Breastfeeding/Lactation Nutrition
- Healthy Eating, Supermarket Shopping Tips, Nutrition Label Reading Tips, Healthier
sub heading under nutrition & diet:
-Vitacover:
--A rebate of $52.95 is available from Vitacover if an EPC ( Enhanced Primary Care)/Chronic Disease Management (CDM) plan is issued by your GP.
--All mandatory paperwork needs to be available at the time of making your appointment for your eligibility.
-Private Health Fund:
--Most private health funds provide rebate on dietetic appointments. However the rebate amount depends on your level of cover. Thus, please contact your health fund to determine your entitled rebate.
-RSB: Approved provider for RSB services

6) FOR DOCTORS: Bright Vale Paediatric Gastroenterologist Referral Form
Bright Vale Dietitian Referral form
7) LOCATIONS & CONTACT

Paediatric Gastroenterology & Hepatology Service
Suite 46
Holy Lantern Bramcote Medical Centre
17 Colin Ferris Pde,
MURDOCH, WA 6150
P: (08) 9422 5061
F: (08) 9422 3094

Nutrition & Diet Service
Suite 46
17 Colin Ferris Pde,
MURDOCH, WA 6150
P: (08) 9422 5061
F: (08) 9422 3094

Tolland Medical Centre
58-60 Karrigan Parkway,
MANDURAH, WA 6210
P: (08) 9647 2283
F: (08) 96724419
www.tmcexample.com.au

This page should have a webform that has following titles:
-Your Name
-Your Email
-Your Phone
-Message

8) NEWS & BLOG
Nice to have
• We liked the design style of the websites below:
https://www.vendoraplex.example/

http://qoravelt.example/

But feel free to use your creativity too
Should not have
• Please do not use any body building or muscle building images

```html
<!DOCTYPE html>
<html lang="en">
<head>
<meta charset="utf-8">
<title>Bright Vale – Health Consulting Services</title>
<link href="https://fonts.googleapis.com/css2?family=Raleway:wght@500;600;700;800;900&family=Open+Sans:wght@400;600;700&display=swap" rel="stylesheet">
<style>
:root{
  --navy:#1d2939;
  --navy-dark:#172231;
  --orange:#faa54b;
  --green:#acd036;
  --ink:#222222;
  --grey:#6b6b6b;
  --pale:#f1f1f1;
  --white:#ffffff;
}
*{margin:0;padding:0;box-sizing:border-box}
html,body{width:759px;height:1200px;overflow:hidden;background:var(--white)}
body{font-family:"Open Sans",Arial,sans-serif;color:var(--ink)}
.page{position:relative;width:759px;height:1200px;overflow:hidden}

/* Header */
.site-header{position:absolute;left:0;top:0;width:759px;height:97px;background:linear-gradient(180deg,var(--navy) 0%,var(--navy-dark) 100%)}
.brand{position:absolute;top:18px;left:0;width:100%;display:flex;justify-content:center;align-items:center;gap:7px}
.brand-dot{width:22px;height:22px;border-radius:50%;background:var(--orange)}
.brand-name{font-family:"Raleway",sans-serif;font-weight:800;font-size:19px;color:var(--green);letter-spacing:.5px}
.main-nav{position:absolute;top:67px;left:0;width:100%;height:30px;border-top:1px solid rgba(255,255,255,.08);display:flex;justify-content:center}
.main-nav a{display:block;height:30px;line-height:30px;padding:0 10px;font-family:"Raleway",sans-serif;font-weight:700;font-size:7.8px;color:var(--white);text-decoration:none;letter-spacing:.2px}
.main-nav a.is-active{background:var(--orange)}

/* Hero */
.hero{position:absolute;left:0;top:97px;width:759px;height:296px;border-top:3px solid var(--green);
  background:linear-gradient(180deg,#bfe0f5 0%,#8fc2e6 35%,#c9b89a 70%,#7f6a45 100%)}
.hero-photo{position:absolute;inset:0}
.hero-kicker{position:absolute;top:93px;width:100%;text-align:center;font-family:"Raleway",sans-serif;font-weight:700;font-size:17px;color:var(--green)}
.hero-title{position:absolute;top:114px;width:100%;text-align:center;font-family:"Raleway",sans-serif;font-weight:900;font-size:45px;color:var(--orange);letter-spacing:.5px}
.hero-rule{position:absolute;top:163px;left:97px;width:565px;height:1px;background:rgba(255,255,255,.55)}
.hero-text{position:absolute;top:177px;width:100%;text-align:center;font-size:8.6px;color:var(--white)}
.hero-button{position:absolute;top:197px;left:342px;width:75px;height:25px;line-height:25px;text-align:center;background:var(--green);color:var(--white);font-family:"Raleway",sans-serif;font-weight:700;font-size:7.5px;letter-spacing:.6px}

/* Services */
.services{position:absolute;left:0;top:393px;width:759px;height:328px;background:var(--white)}
.service{position:absolute;top:48px;width:240px;text-align:center}
.service--nutrition{left:28px}
.service--gut{left:260px}
.service--about{left:491px}
.service-icon{display:block;width:82px;height:82px;margin:0 auto;border-radius:8px;background:linear-gradient(160deg,var(--orange),#f7b96e)}
.service--nutrition .service-icon{background:linear-gradient(160deg,var(--green),var(--orange))}
.service-title{margin-top:28px;font-family:"Raleway",sans-serif;font-weight:600;font-size:11px;color:var(--ink)}
.service-sub{margin-top:3px;font-family:"Raleway",sans-serif;font-weight:600;font-size:7px;letter-spacing:.6px;color:#444}
.service-rule{width:18px;height:1px;background:#cfcfcf;margin:9px auto 0}
.service-text{margin-top:11px;font-size:7px;line-height:13px;color:var(--grey)}
.service-link{display:inline-flex;align-items:center;gap:3px;margin-top:10px;font-size:7px;color:var(--orange);text-decoration:none}

/* Testimonials */
.testimonials{position:absolute;left:0;top:721px;width:759px;height:270px;background:var(--pale);border-top:1px solid #e6e6e6}
.testimonials-backdrop{position:absolute;inset:0;background:linear-gradient(180deg,#ececec,#f6f6f6)}
.section-title{position:absolute;top:43px;width:100%;text-align:center;font-family:"Raleway",sans-serif;font-weight:800;font-size:16px;color:var(--ink)}
.section-title span{color:var(--green)}
.title-ornament{position:absolute;top:68px;left:352px}
.slider-arrow{position:absolute;top:118px;width:28px;height:28px;border-radius:50%;border:1px solid var(--orange);background:var(--white);display:flex;align-items:center;justify-content:center}
.slider-arrow--prev{left:42px}
.slider-arrow--next{left:689px}
.avatar{position:absolute;top:105px;left:345px;width:70px;height:70px;border-radius:50%;border:3px solid var(--orange);background:linear-gradient(160deg,#c8a07c,#8a6a4e)}
.quote{position:absolute;top:176px;width:100%;text-align:center;font-size:12px;line-height:14.5px;color:#555}
.quote-author{position:absolute;top:219px;width:100%;text-align:center;font-size:6.5px;color:var(--orange);letter-spacing:.3px}

/* Footer */
.site-footer{position:absolute;left:0;top:991px;width:759px;height:209px;background:var(--orange);border-top:2px solid var(--green)}
.footer-brand{position:absolute;left:38px;top:60px;display:flex;align-items:center;gap:6px}
.footer-brand-dot{width:14px;height:14px;border-radius:50%;background:var(--white)}
.footer-brand-name{font-family:"Raleway",sans-serif;font-weight:800;font-size:17px;color:var(--white)}
.footer-col{position:absolute;top:46px;color:var(--white)}
.footer-col h3{font-family:"Raleway",sans-serif;font-weight:500;font-size:14px;color:var(--white)}
.footer-about{left:157px;width:220px}
.footer-about p{margin-top:21px;font-size:6.9px;line-height:13.3px}
.footer-links ul{list-style:none;margin-top:10px;padding-left:4px}
.footer-links li{font-size:7.4px;line-height:17.7px}
.footer-site{left:388px}
.footer-support{left:504px}
.footer-network{left:620px}
.footer-strip{position:absolute;left:0;bottom:0;width:759px;height:6px;background:var(--green)}
</style>
</head>
<body>
<div class="page">

  <header class="site-header">
    <div class="brand">
      <span class="brand-dot"></span>
      <span class="brand-name">BRIGHT VALE</span>
    </div>
    <nav class="main-nav">
      <a class="is-active" href="#">HOME</a>
      <a href="#">ABOUT</a>
      <a href="#">NUTRITION AND DIET</a>
      <a href="#">GASTROINTESTINAL HEALTH</a>
      <a href="#">NEWS</a>
      <a href="#">CONTACTS</a>
    </nav>
  </header>

  <section class="hero">
    <div class="hero-photo" role="img" aria-label="Family with children playing outdoors in sunny nature"></div>
    <p class="hero-kicker">HEALTH CONSULTING SERVICES</p>
    <h1 class="hero-title">HEALTH FOR EVERYONE!</h1>
    <div class="hero-rule"></div>
    <p class="hero-text">We need a website design for a new health consulting service called "Bright Vale" based in Perth, Australia.</p>
    <a class="hero-button">READ MORE</a>
  </section>

  <section class="services">
    <article class="service service--nutrition">
      <span class="service-icon" role="img" aria-label="Bathroom scale with footprints icon"></span>
      <h2 class="service-title">Nutrition and Diet</h2>
      <p class="service-sub">CONSULTING SERVICES</p>
      <div class="service-rule"></div>
      <p class="service-text">These consulting services will be provided by an<br>Accredited Dietitian and a Paediatric Gastroenterologist.</p>
      <a class="service-link">read more
        <svg width="7" height="7" viewBox="0 0 10 10"><circle cx="5" cy="5" r="5" fill="#acd036"/><path d="M4 2.8 6.2 5 4 7.2" stroke="#fff" stroke-width="1.4" fill="none"/></svg></a>
    </article>
    <article class="service service--gut">
      <span class="service-icon" role="img" aria-label="Human torso with digestive system icon"></span>
      <h2 class="service-title">Gastrointestinal Health</h2>
      <p class="service-sub">CONSULTING SERVICES</p>
      <div class="service-rule"></div>
      <p class="service-text">These consulting services will be provided by an<br>Accredited Dietitian and a Paediatric Gastroenterologist.</p>
      <a class="service-link">read more
        <svg width="7" height="7" viewBox="0 0 10 10"><circle cx="5" cy="5" r="5" fill="#acd036"/><path d="M4 2.8 6.2 5 4 7.2" stroke="#fff" stroke-width="1.4" fill="none"/></svg></a>
    </article>
    <article class="service service--about">
      <span class="service-icon" role="img" aria-label="Balance with apple and wheat icon"></span>
      <h2 class="service-title">About us</h2>
      <p class="service-sub">CONSULTING SERVICES</p>
      <div class="service-rule"></div>
      <p class="service-text">These consulting services will be provided by an<br>Accredited Dietitian and a Paediatric Gastroenterologist.</p>
      <a class="service-link">read more
        <svg width="7" height="7" viewBox="0 0 10 10"><circle cx="5" cy="5" r="5" fill="#acd036"/><path d="M4 2.8 6.2 5 4 7.2" stroke="#fff" stroke-width="1.4" fill="none"/></svg></a>
    </article>
  </section>

  <section class="testimonials">
    <div class="testimonials-backdrop" role="img" aria-label="Faint grid of customer portrait photos"></div>
    <h2 class="section-title">Our Happy <span>Customers</span></h2>
    <svg class="title-ornament" width="55" height="6" viewBox="0 0 55 6">
      <line x1="3" y1="3" x2="52" y2="3" stroke="#faa54b" stroke-width="1"/>
      <circle cx="3" cy="3" r="2.3" fill="#fff" stroke="#faa54b"/>
      <circle cx="52" cy="3" r="2.3" fill="#fff" stroke="#faa54b"/>
    </svg>
    <span class="slider-arrow slider-arrow--prev">
      <svg width="8" height="10" viewBox="0 0 8 10"><path d="M6 1 2 5l4 4" stroke="#222" stroke-width="1.4" fill="none"/></svg>
    </span>
    <span class="slider-arrow slider-arrow--next">
      <svg width="8" height="10" viewBox="0 0 8 10"><path d="M2 1l4 4-4 4" stroke="#222" stroke-width="1.4" fill="none"/></svg>
    </span>
    <div class="avatar" role="img" aria-label="Customer portrait"></div>
    <p class="quote">We would like to see the website design that uses the colour green and yellowish orange (as the colour of our logo is that).<br>We are open to creative ideas in terms of design, layout, fonts and colours.</p>
    <p class="quote-author">LENA HART</p>
  </section>

  <footer class="site-footer">
    <div class="footer-brand">
      <span class="footer-brand-dot"></span>
      <span class="footer-brand-name">BRIGHT VALE</span>
    </div>
    <div class="footer-col footer-about">
      <h3>About us</h3>
      <p>We would like to see the website design that uses the colour green and yellowish orange (as the colour of our logo is that). We are open to creative ideas in terms of design, layout, fonts and colours. We also would love to see images of nature in the backdrop with families (adults with kids).</p>
    </div>
    <div class="footer-col footer-links footer-site">
      <h3>Site</h3>
      <ul><li>Home</li><li>About us</li><li>Services</li><li>News</li><li>Contact Us</li></ul>
    </div>
    <div class="footer-col footer-links footer-support">
      <h3>Support</h3>
      <ul><li>FAQ's</li><li>Disclaimer</li><li>Support</li><li>Products</li><li>Help</li></ul>
    </div>
    <div class="footer-col footer-links footer-network">
      <h3>Network</h3>
      <ul><li>Friendloop</li><li>Chirpline</li><li>Viewcast</li><li>Snapframe</li><li>Workweave</li></ul>
    </div>
    <div class="footer-strip"></div>
  </footer>

</div>
</body>
</html>
```